International business needs business cards

Our company, DRV Ventures Inc. is in the business of supplying a range construction products with particular emphasis on CEMENT. We have developed our own brand - TORVAN SUPPLIES - with which to infiltrate the market. We are launching our brand of cement (TORVAN Type IS Cement) into the Caribbean which is unlike anything this market has ever seen. A monopoly has existed here for the past 60-odd years and the market has now opened to allow the importation of other brands and consumers are anxious and ready for change/improvement. We are very excited to be launching and want to make a great first impression. We will be conducting workshops and seminars (from government level to the hardware store owners) and we want our business card to give us the strong, confident introduction that we need.

Target Market(s)

construction; builders; engineers; home owners

Industry/Entity Type

Construction

Contact Information for Business Card

Marisol Depree
CEO
cell # 1 555 4180736
Ground floor,Lindell Plaza Suite 2734
George Town,Grand Cayman
Cayman Islands,KY1-4823
EMAIL: m.depree@drvventuresinc.example
web site drvventuresinc.example

COMPANY: skype info drv.ventures.example

second card
Yvette Brannock-Depree
CFO
CELL# 1 555 607 3941
George Town,Grand Cayman
Cayman Islands,KY1-4823
EMAIL: y.brannockdepree@drvventuresinc.example
website drvventuresinc.example

Requirements
Must have
• Business cards must display BOTH logos - DRV is the company and TORVAN is the brand.

```html
<!DOCTYPE html>
<html lang="en">
<head>
<meta charset="utf-8">
<title>DRV Ventures Inc. — Business Cards</title>
<link href="https://fonts.googleapis.com/css2?family=Open+Sans:wght@400;600;700&display=swap" rel="stylesheet">
<style>
  :root {
    --page-bg: #4a4440;
    --card-bg: #121212;
    --card-edge: #000000;
    --text-main: #ffffff;
    --text-soft: #e6e6e6;
    --mark-red: #8f1a1c;
    --mark-grey: #6f6f6f;
  }
  * { box-sizing: border-box; margin: 0; padding: 0; }
  html, body {
    width: 1200px; height: 844px; overflow: hidden;
    background: var(--page-bg);
    font-family: "Open Sans", Arial, sans-serif;
  }
  .sheet {
    width: 1200px; height: 844px;
    display: flex; align-items: center; justify-content: center; gap: 40px;
  }
  .card {
    position: relative;
    width: 540px; height: 310px;
    background: var(--card-bg);
    border: 1px solid var(--card-edge);
    color: var(--text-main);
    box-shadow: 0 8px 22px rgba(0,0,0,0.45);
  }
  .company-mark {
    position: absolute;
    display: flex; align-items: center; gap: 12px;
  }
  .company-mark__square {
    width: 62px; height: 62px; background: var(--mark-red);
  }
  .company-mark__name {
    font-weight: 700; font-size: 30px; line-height: 1.05; color: var(--text-main);
  }
  .card--front .company-mark { left: 150px; top: 58px; }
  .contact-list {
    position: absolute; right: 28px; top: 118px;
    list-style: none; text-align: right;
    font-size: 12.5px; line-height: 21px; color: var(--text-soft);
  }
  .contact-list li { display: flex; justify-content: flex-end; align-items: center; gap: 8px; }
  .contact-list svg { width: 11px; height: 11px; flex: none; }
  .holder {
    position: absolute; left: 30px; bottom: 30px;
  }
  .holder__name { font-weight: 700; font-size: 19px; line-height: 1.2; }
  .holder__role { font-size: 12.5px; margin-bottom: 14px; color: var(--text-soft); }
  .holder__address { font-style: normal; font-size: 14px; line-height: 21px; color: var(--text-soft); }
  .card--back .company-mark { left: 130px; top: 80px; }
  .brand-mark {
    position: absolute; left: 0; right: 0; top: 190px;
    display: flex; flex-direction: column; align-items: center; gap: 6px;
  }
  .brand-mark__circle {
    width: 30px; height: 30px; border-radius: 50%; background: var(--mark-grey);
  }
  .brand-mark__name {
    font-size: 10px; font-weight: 600; letter-spacing: 1px; color: var(--mark-grey);
  }
</style>
</head>
<body>
<main class="sheet">
  <section class="card card--front">
    <div class="company-mark">
      <span class="company-mark__square"></span>
      <span class="company-mark__name">DRV Ventures Inc.</span>
    </div>
    <ul class="contact-list">
      <li>1 555 4180736
        <svg viewBox="0 0 12 12" aria-hidden="true"><path d="M2.5 1 L4.5 1 L5.2 3.5 L4 4.5 Q5 7 7.5 8 L8.5 6.8 L11 7.5 L11 9.5 Q10 11 8.5 11 Q2 9.5 1 3.5 Q1 2 2.5 1 Z" fill="#fff"/></svg>
      </li>
      <li>m.depree@drvventuresinc.example
        <svg viewBox="0 0 12 12" aria-hidden="true"><rect x="1" y="2.5" width="10" height="7" fill="#fff"/><path d="M1 2.5 L6 6.5 L11 2.5" stroke="#121212" stroke-width="1" fill="none"/></svg>
      </li>
      <li>www.drvventuresinc.example
        <svg viewBox="0 0 12 12" aria-hidden="true"><circle cx="6" cy="6" r="5" fill="#fff"/><path d="M1 6 H11 M6 1 Q3 6 6 11 Q9 6 6 1" stroke="#121212" stroke-width="0.9" fill="none"/></svg>
      </li>
    </ul>
    <div class="holder">
      <p class="holder__name">Marisol Depree</p>
      <p class="holder__role">CEO</p>
      <address class="holder__address">
        Ground floor, Lindell Plaza Suite 2734<br>
        George Town, Grand Cayman<br>
        Cayman Islands, KY1-4823
      </address>
    </div>
  </section>

  <section class="card card--back">
    <div class="company-mark">
      <span class="company-mark__square"></span>
      <span class="company-mark__name">DRV Ventures Inc.</span>
    </div>
    <div class="brand-mark">
      <span class="brand-mark__circle"></span>
      <span class="brand-mark__name">TORVAN SUPPLIES</span>
    </div>
  </section>
</main>
</body>
</html>
```